Business cards and stationary design

We just completed the design of our new logo and we need to print new business cards and letterhead for our nonprofit. We are looking for a fresh new design that shows off our new logo. On letterhead, we must have a column on the right or left to include our Board of Directors (up to 45 names) (see attachment)

Industry/Entity Type

Non-Profit

Contact Information for Business Card

Standard business card with name, title, Company name, mailing address phone numbers, email address and website. Tagline on back "Bringing the homeless home"

Font styles to use
Sans Serif

Requirements
Must have
• include pertinent information above
• new logo
• fonts compatible with logo
• should use logo colors only
Nice to have
• tag lines

```html
<!DOCTYPE html>
<html lang="en">
<head>
<meta charset="utf-8">
<title>Harbor Home Alliance – Business Card</title>
<link href="https://fonts.googleapis.com/css2?family=Exo+2:wght@500;600;700&family=Roboto:wght@400&display=swap" rel="stylesheet">
<style>
  :root {
    --backdrop: #2a2a2a;
    --teal: #0b82a3;
    --red: #d42027;
    --paper: #f2f2f2;
    --ink: #4a4a4a;
    --white: #ffffff;
  }
  * { margin: 0; padding: 0; box-sizing: border-box; }
  html, body { width: 1200px; height: 960px; overflow: hidden; }
  body {
    background: var(--backdrop);
    position: relative;
    font-family: "Exo 2", sans-serif;
  }
  .card {
    position: absolute;
    width: 600px;
    height: 342px;
  }
  /* Back side */
  .card-back {
    left: 322px; top: 108px;
    background: var(--teal);
    color: var(--white);
  }
  .card-back .brand {
    position: absolute;
    left: 0; right: 0; top: 150px;
    display: flex; align-items: center; justify-content: center; gap: 14px;
    font-family: "Exo 2", sans-serif;
    font-weight: 700;
    font-size: 30px;
    letter-spacing: 2px;
    color: var(--white);
  }
  .brand-square {
    width: 22px; height: 22px;
    background: var(--white);
  }
  .card-back .url {
    position: absolute;
    left: 0; right: 0; top: 291px;
    text-align: center;
    font-family: "Roboto", sans-serif;
    font-size: 14px;
    letter-spacing: 5.2px;
  }
  /* Front side */
  .card-front {
    left: 320px; top: 493px;
    background: var(--paper);
  }
  .card-front .brand {
    position: absolute;
    left: 35px; top: 98px;
    display: flex; align-items: center; gap: 10px;
    font-weight: 600;
    font-size: 20px;
    letter-spacing: 2px;
    color: var(--teal);
  }
  .card-front .brand-square { width: 14px; height: 14px; background: var(--teal); }
  .rule {
    position: absolute;
    left: 32px; top: 128px;
    width: 536px; height: 1px;
    background: var(--red);
  }
  .person {
    position: absolute;
    right: 30px; top: 78px;
    text-align: right;
  }
  .person-name {
    font-weight: 600;
    font-size: 21px;
    color: var(--teal);
    line-height: 1;
  }
  .person-title {
    font-weight: 600;
    font-size: 14px;
    color: var(--red);
    margin-top: 6px;
  }
  .contacts {
    position: absolute;
    left: 30px; top: 259px;
    list-style: none;
    font-weight: 600;
    font-size: 13.5px;
    color: var(--ink);
  }
  .contacts li {
    display: flex; align-items: center; gap: 8px;
    height: 19.5px;
  }
  .contacts svg { width: 13px; height: 13px; fill: var(--teal); }
  .address {
    position: absolute;
    right: 30px; top: 259px;
    text-align: right;
    font-style: normal;
    font-weight: 600;
    font-size: 13.5px;
    line-height: 19.5px;
    color: var(--ink);
  }
</style>
</head>
<body>

<section class="card card-back">
  <div class="brand"><span class="brand-square"></span>HARBOR HOME ALLIANCE</div>
  <p class="url">www.harborhome.org</p>
</section>

<section class="card card-front">
  <div class="brand"><span class="brand-square"></span>HARBOR HOME ALLIANCE</div>
  <div class="rule"></div>

  <div class="person">
    <p class="person-name">DANIEL REYES</p>
    <p class="person-title">CEO/FOUNDER</p>
  </div>

  <ul class="contacts">
    <li>
      <svg viewBox="0 0 16 16" aria-hidden="true"><path d="M3.6 1.2l2.3 2.6c.4.4.4 1 0 1.4L4.7 6.4c.9 2 2.5 3.6 4.6 4.6l1.2-1.2c.4-.4 1-.4 1.4 0l2.6 2.3c.4.4.4 1 0 1.4l-1.3 1.3c-.6.6-1.5.8-2.3.5C6 13.7 2.3 10 .7 5.2.4 4.4.6 3.5 1.2 2.9L2.2 1.2c.4-.4 1-.4 1.4 0z"/></svg>
      555 214 7730
    </li>
    <li>
      <svg viewBox="0 0 16 16" aria-hidden="true"><path d="M1 3h14v1.2L8 8.6 1 4.2z"/><path d="M1 5.6l7 4.4 7-4.4V13H1z"/></svg>
      daniel@harborhome.org
    </li>
    <li>
      <svg viewBox="0 0 16 16" aria-hidden="true"><circle cx="8" cy="8" r="7"/><path d="M4 5.5c1.5-.5 2.5.5 2 1.8-.4 1 .8 1.7 1.5 2.5.6.8 0 2-.8 2.8M10 2.5c-.5 1 .3 1.8 1.3 1.8s1.7 1 1.2 2" stroke="#f2f2f2" stroke-width="1.2" fill="none"/></svg>
      www.harborhome.org
    </li>
  </ul>

  <address class="address">
    Harbor Home Alliance<br>
    1420 Birchwood Lane<br>
    Fairview, Alaska 99508
  </address>
</section>

</body>
</html>
```